Small Business Broker Business Card Design

A business card design for a small business brokerage, which is a financial service, not unlike real estate brokerage, but for small businesses such as laundromats, pizza shops, restaurants, cleaners etc. The designs should all be simple, more conservative in nature, using the colors and font of the logo. Again, think real estate Brokerage as a business context
Contact Information for Business Card
Name: Glen R. Harlow. Title: Small Business Advisor. Email: g.harlow@bayfieldcapitalworks.example. Mobile: (555) 274-3918. Office: (555) 806-2147. www.bayfieldcapitalworks.example

```html
<!DOCTYPE html>
<html lang="en">
<head>
<meta charset="utf-8">
<title>Bayfield Capital Works – Business Card</title>
<link rel="stylesheet" href="https://fonts.googleapis.com/css2?family=Montserrat:wght@600;700&family=Arimo:wght@400&display=swap">
<style>
  :root {
    --page: #151617;
    --navy: #15305f;
    --navy-deep: #112751;
    --navy-pattern: #1c3a70;
    --green: #72c02c;
    --white: #ffffff;
  }
  * { box-sizing: border-box; margin: 0; padding: 0; }
  html, body { width: 1200px; height: 963px; overflow: hidden; background: var(--page); }
  .canvas { position: relative; width: 1200px; height: 963px; }

  .card {
    position: absolute; left: 220px; width: 760px; height: 434px;
    border-radius: 26px; overflow: hidden;
    background: linear-gradient(160deg, var(--navy) 0%, var(--navy-deep) 100%);
  }
  .card--front { top: 40px; }
  .card--back { top: 500px; }

  .brand__name {
    font: 700 20px/1.1 "Montserrat", sans-serif; color: var(--white);
    letter-spacing: 0.04em; text-transform: uppercase; white-space: nowrap;
  }
  .brand__tagline {
    margin-top: 5px; font: 600 9.5px/1.2 "Montserrat", sans-serif; color: var(--green);
    letter-spacing: 0.1em; text-transform: uppercase; white-space: nowrap;
  }

  /* front */
  .brand { position: absolute; left: 64px; top: 92px; }
  .rule { position: absolute; left: 0; top: 140px; width: 760px; height: 20px; }

  .person { position: absolute; right: 48px; top: 40px; text-align: right; }
  .person__name {
    font: 700 26px/1.1 "Montserrat", sans-serif; color: var(--white);
    letter-spacing: 0.05em; text-transform: uppercase; white-space: nowrap;
  }
  .person__title { margin-top: 6px; font: 400 18px/1.2 "Arimo", sans-serif; color: var(--green); white-space: nowrap; }
  .person__mark { position: absolute; right: 0; top: 52px; width: 22px; height: 44px; background: var(--green); }

  .contacts { position: absolute; left: 48px; top: 196px; list-style: none; }
  .contacts li {
    display: flex; align-items: center; gap: 12px; margin-bottom: 12px;
    font: 400 18px/1.2 "Arimo", sans-serif; color: var(--white);
  }
  .contacts svg { width: 18px; height: 18px; flex: none; }

  /* back */
  .pattern-field { position: absolute; inset: 0; background: linear-gradient(160deg, var(--navy-pattern) 0%, var(--navy) 100%); }
  .back-brand { position: absolute; left: 0; right: 0; top: 182px; display: flex; justify-content: center; align-items: center; gap: 16px; }
  .back-brand__square { width: 30px; height: 30px; background: var(--green); }
  .back-brand .brand__name { font-size: 28px; }
  .back-brand .brand__tagline { font-size: 11px; }
</style>
</head>
<body>
<main class="canvas">

  <section class="card card--front" aria-label="Business card front">
    <div class="person">
      <p class="person__name">Glen R. Harlow</p>
      <p class="person__title">Small Business Advisor</p>
    </div>
    <span class="person__mark" aria-hidden="true"></span>

    <div class="brand">
      <p class="brand__name">Bayfield Capital Works, Inc</p>
      <p class="brand__tagline">Confidently buy or sell a local business today</p>
    </div>

    <svg class="rule" viewBox="0 0 760 20" aria-hidden="true">
      <rect x="0" y="4" width="40" height="7" fill="var(--green)"/>
      <rect x="490" y="4" width="270" height="7" fill="var(--green)"/>
      <rect x="0" y="12" width="760" height="2" fill="var(--white)"/>
    </svg>

    <ul class="contacts">
      <li>
        <svg viewBox="0 0 24 24" aria-hidden="true"><path d="M6.6 10.8a15 15 0 0 0 6.6 6.6l2.2-2.2a1 1 0 0 1 1-.25 11.4 11.4 0 0 0 3.6.6 1 1 0 0 1 1 1V20a1 1 0 0 1-1 1A17 17 0 0 1 3 4a1 1 0 0 1 1-1h3.5a1 1 0 0 1 1 1c0 1.25.2 2.45.6 3.6a1 1 0 0 1-.25 1z" fill="var(--green)"/></svg>
        (555) 806-2147
      </li>
      <li>
        <svg viewBox="0 0 24 24" aria-hidden="true"><rect x="6" y="2" width="12" height="20" rx="2" fill="none" stroke="var(--green)" stroke-width="2"/><circle cx="12" cy="18" r="1.2" fill="var(--green)"/></svg>
        (555) 274-3918
      </li>
      <li>
        <svg viewBox="0 0 24 24" aria-hidden="true"><rect x="2" y="5" width="20" height="14" rx="1.5" fill="none" stroke="var(--green)" stroke-width="2"/><path d="M2.5 6l9.5 7 9.5-7" fill="none" stroke="var(--green)" stroke-width="2"/></svg>
        g.harlow@bayfieldcapitalworks.example
      </li>
      <li>
        <svg viewBox="0 0 24 24" aria-hidden="true"><circle cx="12" cy="12" r="9.5" fill="none" stroke="var(--green)" stroke-width="2"/><path d="M2.5 12h19M12 2.5c3 3 3 16 0 19M12 2.5c-3 3-3 16 0 19" fill="none" stroke="var(--green)" stroke-width="1.6"/></svg>
        www.bayfieldcapitalworks.example
      </li>
    </ul>
  </section>

  <section class="card card--back" aria-label="Business card back">
    <div class="pattern-field" role="img" aria-label="Embossed repeating pattern in tones of navy blue"></div>
    <div class="back-brand">
      <span class="back-brand__square" aria-hidden="true"></span>
      <div>
        <p class="brand__name">Bayfield Capital Works, Inc</p>
        <p class="brand__tagline">Confidently buy or sell a local business today</p>
      </div>
    </div>
  </section>

</main>
</body>
</html>
```